IT Company requires new Business Card design.

Over the years we have had a few different business card designs. We are now due for new cards across the board for all staff. We felt this would be a good time to start fresh with a new design. Our traditional card simply had our details on the front, and a list of services on the back. We don't particularly need the list of services, we have had cards where the only thing on the rear of the card was our logo.
Feel free to be creative, we would like our tag line "Complete IT Management" to appear at some point, doesn't necessarily have to be with the logo.
I have attached samples and drafts of various previous cards we have used over the years.

```html
<!DOCTYPE html>
<html lang="en">
<head>
<meta charset="utf-8">
<title>Riverstone Systems – Business Card</title>
<link rel="stylesheet" href="https://fonts.googleapis.com/css2?family=Open+Sans:wght@400;600;700;800&display=swap">
<style>
  :root {
    --backdrop: #e6e3df;
    --card: #ffffff;
    --slate: #63737e;
    --slate-dark: #4f5d67;
    --ink: #3a3a3a;
    --rule: #555d63;
    --band-text: #ffffff;
  }
  * { box-sizing: border-box; margin: 0; padding: 0; }
  html, body {
    width: 1034px; height: 1200px; overflow: hidden;
    background: var(--backdrop);
    font-family: "Open Sans", Arial, sans-serif;
  }
  .card {
    position: absolute; left: 75px; width: 899px; height: 511px;
    background: var(--card);
    box-shadow: 0 2px 8px rgba(0,0,0,0.18);
  }
  .card--front { top: 69px; }
  .card--back { top: 631px; }

  .brand {
    position: absolute; left: 0; right: 0; top: 60px;
    display: flex; justify-content: center; align-items: center; gap: 26px;
  }
  .brand__square { width: 110px; height: 110px; background: var(--slate); }
  .brand__name {
    font-weight: 800; color: var(--slate); line-height: 0.95;
    font-size: 62px; letter-spacing: 1px; text-transform: uppercase;
  }

  .holder {
    position: absolute; right: calc(899px - 401px); top: 262px;
    text-align: right; color: var(--ink);
  }
  .holder__name { font-size: 27px; font-weight: 700; color: var(--slate-dark); line-height: 1.2; }
  .holder__role { font-size: 21px; color: #555; margin-top: 2px; }
  .holder__address { font-size: 21px; margin-top: 16px; line-height: 1.45; color: var(--ink); }

  .divider {
    position: absolute; left: 424px; top: 254px; width: 1px; height: 166px;
    background: #b9bec2;
  }

  .contacts {
    position: absolute; left: 444px; top: 252px; list-style: none;
    font-size: 21px; color: var(--ink);
  }
  .contacts li { display: flex; align-items: center; gap: 10px; height: 35px; }
  .contacts svg { width: 20px; height: 20px; fill: var(--slate-dark); flex: none; }

  .rule {
    position: absolute; left: 0; right: 0; top: 443px; height: 5px; background: var(--rule);
  }
  .tagline {
    position: absolute; left: 0; right: 0; top: 458px; height: 53px;
    background: var(--slate); color: var(--band-text);
    display: flex; align-items: center; justify-content: center;
    font-size: 23px; letter-spacing: 4.5px; text-transform: uppercase;
  }

  .back-brand {
    position: absolute; left: 0; right: 0; top: 150px;
    display: flex; justify-content: center; align-items: center; gap: 30px;
  }
  .back-brand__square { width: 150px; height: 150px; background: var(--slate); }
  .back-brand__name {
    font-weight: 800; color: var(--slate); line-height: 0.95;
    font-size: 74px; text-transform: uppercase; letter-spacing: 1px;
  }
  .back-url {
    position: absolute; left: 0; right: 0; top: 462px; text-align: center;
    font-size: 25px; letter-spacing: 2px; color: var(--ink);
  }
</style>
</head>
<body>

<section class="card card--front">
  <div class="brand">
    <div class="brand__square"></div>
    <div class="brand__name">Riverstone<br>Systems</div>
  </div>

  <div class="holder">
    <p class="holder__name">Daniel Hart</p>
    <p class="holder__role">Operation Manager</p>
    <p class="holder__address">Unit 7 22 Marlow Street<br>Greenfield WA 6190</p>
  </div>

  <div class="divider"></div>

  <ul class="contacts">
    <li>
      <svg viewBox="0 0 20 20" aria-hidden="true"><circle cx="10" cy="10" r="9" fill="none" stroke="#4f5d67" stroke-width="1.6"/><path d="M6.5 5.5l2 0 .8 2.4-1.2 1c.6 1.3 1.6 2.3 2.9 2.9l1-1.2 2.4.8 0 2c-4.5.3-8.2-3.4-7.9-7.9z"/></svg>
      08 5550 1840
    </li>
    <li>
      <svg viewBox="0 0 20 20" aria-hidden="true"><rect x="5" y="1" width="10" height="18" rx="2"/><rect x="7" y="3.5" width="6" height="6" fill="#fff"/><rect x="7" y="11.5" width="6" height="5" fill="#fff" opacity=".5"/></svg>
      0400 555 718
    </li>
    <li>
      <svg viewBox="0 0 20 20" aria-hidden="true"><rect x="5" y="2" width="10" height="6" fill="none" stroke="#4f5d67" stroke-width="1.6"/><rect x="1" y="8" width="18" height="8" rx="1.5"/><rect x="5" y="13" width="10" height="5"/></svg>
      08 5550 1840
    </li>
    <li>
      <svg viewBox="0 0 20 20" aria-hidden="true"><rect x="1" y="4" width="18" height="13" rx="1.5"/><path d="M2 5l8 6 8-6" fill="none" stroke="#fff" stroke-width="1.6"/></svg>
      daniel@riverstonesystems.com.au
    </li>
    <li>
      <svg viewBox="0 0 20 20" aria-hidden="true"><circle cx="10" cy="10" r="8.5" fill="none" stroke="#4f5d67" stroke-width="1.6"/><ellipse cx="10" cy="10" rx="3.5" ry="8.5" fill="none" stroke="#4f5d67" stroke-width="1.4"/><path d="M1.5 10h17M3 5.5h14M3 14.5h14" stroke="#4f5d67" stroke-width="1.2"/></svg>
      www.riverstonesystems.com.au
    </li>
  </ul>

  <div class="rule"></div>
  <div class="tagline">Complete IT Management</div>
</section>

<section class="card card--back">
  <div class="back-brand">
    <div class="back-brand__square"></div>
    <div class="back-brand__name">Riverstone<br>Systems</div>
  </div>
  <p class="back-url">www.riverstonesystems.com.au</p>
</section>

</body>
</html>
```